Plakat-Design 24h Betreuung
Zielgruppe
Wir vermitteln 24h Pflege- und Betreuungskräfte für alte und hilfbedürftige Menschen!
Zielgruppe: deren Angehörige (zwischen 50-70 Jahre alt)
Aufgabenstellung
Klare Ansage - nicht zu verspielt - geradlinig
Maße Plakat: 504 cm breit x 238 cm hoch
Das PLAKAT ist ca 10 m von der Straße entfernet und ist für Autofahrer gedacht - somit muss man alles gut lesen können und groß geschrieben sein !!!!
Folgender Text und Bilder sollte das Plakat beinhalten:
24h - Betreuung (groß links oben platziert)
Logo: SorgeFreund.at
Foto mit 10 Personen
Erfahrung seit 2010
www.sorgefreund.at

```html
<!DOCTYPE html>
<html lang="de">
<head>
<meta charset="utf-8">
<title>24h - Betreuung | SorgeFreund.at</title>
<link rel="stylesheet" href="https://fonts.googleapis.com/css2?family=Rubik:wght@500;700&display=swap">
<style>
  :root {
    --frame-grey: #dfdfdd;
    --paper: #ffffff;
    --brand-blue: #2b4280;
    --brand-orange: #d4691f;
    --photo-light: #f4f5f8;
    --photo-mid: #cbd1de;
    --photo-deep: #4a5a8a;
  }
  html, body {
    margin: 0;
    padding: 0;
    width: 1200px;
    height: 704px;
    overflow: hidden;
    background: var(--frame-grey);
    font-family: "Rubik", Arial, sans-serif;
  }
  .poster {
    position: absolute;
    left: 71px;
    top: 70px;
    width: 1058px;
    height: 563px;
    background: var(--paper);
    overflow: hidden;
  }
  .headline {
    position: absolute;
    left: 46px;
    top: 32px;
    margin: 0;
    font-size: 80px;
    font-weight: 700;
    line-height: 1;
    color: var(--brand-blue);
    white-space: nowrap;
  }
  .experience {
    position: absolute;
    left: 46px;
    top: 123px;
    margin: 0;
    font-size: 38px;
    font-weight: 700;
    line-height: 1;
    color: var(--brand-orange);
    letter-spacing: 0.3px;
    white-space: nowrap;
  }
  .brand-name {
    position: absolute;
    left: 43px;
    top: 455px;
    margin: 0;
    font-size: 44px;
    font-weight: 500;
    line-height: 1;
    color: var(--brand-blue);
    white-space: nowrap;
  }
  .team-photo {
    position: absolute;
    left: 464px;
    top: 120px;
    width: 571px;
    height: 420px;
    background: linear-gradient(180deg, var(--photo-light) 0%, var(--photo-mid) 55%, var(--photo-deep) 100%);
  }
  .color-band {
    position: absolute;
    left: 0;
    bottom: 0;
    width: 100%;
    height: 14px;
    display: flex;
  }
  .color-band .band-blue {
    width: 471px;
    background: var(--brand-blue);
  }
  .color-band .band-orange {
    flex: 1;
    background: var(--brand-orange);
  }
</style>
</head>
<body>
  <main class="poster">
    <h1 class="headline">24h - Betreuung</h1>
    <p class="experience">Erfahrung seit 2010</p>
    <div class="team-photo" role="img" aria-label="Gruppenfoto des Teams: zehn Personen in weißen Blusen mit blauen Halstüchern und Jeans, vorne eine Frau im blauen Kostüm und ein Mann im dunklen Sakko, vor weißem Hintergrund"></div>
    <p class="brand-name">SorgeFreund.at</p>
    <div class="color-band">
      <span class="band-blue"></span>
      <span class="band-orange"></span>
    </div>
  </main>
</body>
</html>
```